KDWB Business Card

Looking for a business card design to incorporate our branding. We want to only use the colors listing in the Branding Package (attached).
Updates

Target Market(s)

People who need their phone or device fixed.

Industry/Entity Type

Electronics

Contact Information for Business Card

Please use:

Brightwick Gadget Clinic LLC
4810 E Harlow Ridge Rd
Suite 417
San Antonio, TX 78163

Marcus Delgrove, Store Manager

(210) 555-0147

Requirements
Must have
• Must include the colors that are contained within the Branding Package PDF file.

```html
<!DOCTYPE html>
<html lang="en">
<head>
<meta charset="utf-8">
<title>Brightwick Gadget Clinic – Business Card</title>
<link rel="stylesheet" href="https://fonts.googleapis.com/css2?family=Arimo:wght@400;700&display=swap">
<style>
  :root {
    --canvas-bg: #e9e9eb;
    --card-bg: #ffffff;
    --brand-orange: #f05a22;
    --brand-tint: #fdf1eb;
    --ink: #3a3a3a;
    --ink-soft: #555555;
    --card-shadow: 0 6px 18px rgba(0,0,0,0.12);
  }
  * { box-sizing: border-box; margin: 0; padding: 0; }
  html, body { width: 1200px; height: 873px; overflow: hidden; }
  body {
    background: var(--canvas-bg);
    font-family: "Arimo", Arial, sans-serif;
    color: var(--ink);
    position: relative;
  }
  .card {
    position: absolute;
    width: 525px;
    height: 300px;
    background: var(--card-bg);
    box-shadow: var(--card-shadow);
    overflow: hidden;
  }
  .card--front { left: 50px; top: 286px; }
  .card--back  { left: 625px; top: 286px; }

  .tint-panel {
    position: absolute;
    left: 28px; top: 22px;
    width: 250px; height: 256px;
    background: var(--brand-tint);
    border-radius: 44px;
  }
  .brand {
    position: absolute;
    display: flex;
    align-items: center;
    gap: 10px;
  }
  .brand__square {
    width: 30px; height: 30px;
    background: var(--brand-orange);
    border-radius: 6px;
    flex: none;
  }
  .brand__name {
    color: var(--brand-orange);
    font-weight: 400;
    font-size: 19px;
    line-height: 1.15;
  }
  .card--front .brand { left: 52px; top: 112px; width: 210px; }
  .card--back .brand { left: 0; right: 0; top: 128px; justify-content: center; }
  .card--back .brand__square { width: 40px; height: 40px; border-radius: 8px; }
  .card--back .brand__name { font-size: 26px; }

  .person {
    position: absolute;
    right: 32px; top: 128px;
    text-align: right;
  }
  .person__name { font-size: 22px; color: var(--ink); letter-spacing: -0.2px; }
  .person__title { font-size: 12px; color: var(--brand-orange); margin-top: 4px; }

  .contact {
    position: absolute;
    right: 32px; bottom: 30px;
    text-align: right;
    font-size: 11.5px;
    color: var(--ink-soft);
    line-height: 1.45;
  }
  .contact__row { display: flex; justify-content: flex-end; align-items: flex-start; gap: 8px; }
  .contact__row + .contact__row { margin-top: 4px; }
  .contact__icon {
    width: 13px; height: 13px;
    background: var(--brand-orange);
    border-radius: 2px;
    flex: none;
    margin-top: 2px;
    display: flex; align-items: center; justify-content: center;
  }
</style>
</head>
<body>
  <section class="card card--front" aria-label="Business card front">
    <div class="tint-panel"></div>
    <div class="brand">
      <span class="brand__square"></span>
      <span class="brand__name">Brightwick Gadget Clinic</span>
    </div>
    <div class="person">
      <p class="person__name">Marcus Delgrove</p>
      <p class="person__title">Store Manager</p>
    </div>
    <div class="contact">
      <div class="contact__row">
        <span>(210) 555-0147</span>
        <span class="contact__icon">
          <svg width="9" height="9" viewBox="0 0 24 24" aria-hidden="true"><path fill="#fff" d="M6.6 10.8a15 15 0 0 0 6.6 6.6l2.2-2.2a1 1 0 0 1 1-.25 11.4 11.4 0 0 0 3.6.6 1 1 0 0 1 1 1V20a1 1 0 0 1-1 1A17 17 0 0 1 3 4a1 1 0 0 1 1-1h3.5a1 1 0 0 1 1 1c0 1.25.2 2.45.6 3.6a1 1 0 0 1-.25 1z"/></svg>
        </span>
      </div>
      <div class="contact__row">
        <span>4810 E Harlow Ridge Rd<br>Suite 417, San Antonio, TX 78163</span>
        <span class="contact__icon">
          <svg width="9" height="9" viewBox="0 0 24 24" aria-hidden="true"><path fill="#fff" d="M12 2a7 7 0 0 0-7 7c0 5.2 7 13 7 13s7-7.8 7-13a7 7 0 0 0-7-7zm0 9.5A2.5 2.5 0 1 1 12 6.5a2.5 2.5 0 0 1 0 5z"/></svg>
        </span>
      </div>
    </div>
  </section>

  <section class="card card--back" aria-label="Business card back">
    <div class="brand">
      <span class="brand__square"></span>
      <span class="brand__name">Brightwick Gadget Clinic</span>
    </div>
  </section>
</body>
</html>
```